QP Fiduciary Website Redesign Contest

We want to refresh our website to be more insitutional, professional for an international audience. We have designed a new logo for this purpose and that has been attached. A full brand brief and positioning statement has also been attached. Please read through all the documents carefully before designing. The old website is found here: https://qp-fiduciary.example/

Target Market(s)

Actuaries and associated businesses internationally

Industry/Entity Type

professional services - actuaries

Number of Pages Required

3 page

Font styles to use
Sans Serif

Colors
0054AA
0677BA
7BADD7
CADEEF
E8F1F8
0094D4
00A9DD
6FCCEA
C7EBF8
E9F6FB
F0912C
F2A743
F7CA91
FBE8D2
FDF5EE
EE7325
F08F49
F5BC92
FAE3D3
FDF4ED
EB3D1F
EC4F4E
F09395
F8D3D4
FCEDEE

Requirements
Must have
• blues and greens to match the logo color, complimentary colors, navigation
Nice to have
• old site: https://qp-fiduciary.example/

```html
<!DOCTYPE html>
<html lang="en">
<head>
<meta charset="utf-8">
<title>QP Fiduciary — Actuarial Software</title>
<link href="https://fonts.googleapis.com/css2?family=Poppins:wght@300;400;500;600;700&display=swap" rel="stylesheet">
<style>
:root{
  --navy:#0b1b4a;
  --navy-deep:#08143a;
  --blue:#0054AA;
  --blue-mid:#0677BA;
  --sky:#0094D4;
  --teal:#109e8c;
  --teal-dark:#0c8a7e;
  --orange:#EE7325;
  --orange-light:#F2A743;
  --band:#eef1fb;
  --text:#1a1f36;
  --muted:#4a4f63;
  --line:#e3e7f0;
  --white:#ffffff;
}
*{margin:0;padding:0;box-sizing:border-box}
html,body{width:1200px;height:4515px;overflow:hidden}
body{font-family:'Poppins',sans-serif;color:var(--text);background:var(--white)}
.page{position:relative;width:1200px;height:4515px;overflow:hidden}
.abs{position:absolute}
.brand{font-family:'Poppins',sans-serif;font-weight:600;letter-spacing:2px;display:flex;align-items:center;gap:10px;white-space:nowrap}
.brand .dot{width:14px;height:14px;border-radius:50%;background:var(--orange)}
.btn{position:absolute;display:flex;align-items:center;justify-content:space-between;border-radius:30px;color:var(--white);font-weight:500;text-transform:uppercase;font-size:12px;letter-spacing:.3px;background:linear-gradient(90deg,var(--teal),var(--blue));padding:0 6px 0 16px}
.btn .arrow{width:32px;height:32px;border-radius:50%;background:var(--white);display:flex;align-items:center;justify-content:center}
.badge{position:absolute;left:50%;transform:translateX(-50%);border:1px solid #9fd4cc;background:#e7f6f3;color:var(--teal-dark);font-size:11.5px;border-radius:20px;padding:5px 18px;text-transform:uppercase;white-space:nowrap}
.section-title{position:absolute;left:0;width:1200px;text-align:center;font-size:37px;font-weight:400;color:var(--text)}
.section-title b{font-weight:600}
.section-desc{position:absolute;left:0;width:1200px;text-align:center;font-size:12.5px;line-height:22px;color:var(--text)}

/* header */
.header{position:absolute;top:0;left:0;width:1200px;height:81px;background:var(--white)}
.nav{position:absolute;top:32px;left:352px;display:flex;gap:24px;font-size:12.5px;font-weight:500;color:var(--navy)}

/* hero */
.hero-photo{position:absolute;top:81px;left:0;width:1200px;height:620px;background:linear-gradient(100deg,#2a2630 0%,#4a4540 35%,#6b5e50 60%,#8a7a66 80%,#5a5048 100%)}
.hero-shade{position:absolute;top:81px;left:0;width:1200px;height:620px;background:linear-gradient(90deg,rgba(10,14,30,.75) 0%,rgba(10,14,30,.45) 45%,rgba(10,14,30,0) 75%)}
.hero-title{position:absolute;top:214px;left:91px;color:var(--white);font-size:49px;line-height:49px;font-weight:300}
.hero-title b{font-weight:600}
.hero-sub{position:absolute;top:372px;left:91px;color:var(--white);font-size:12.5px;line-height:20px;width:470px}

/* overview */
.ov-card{position:absolute;top:963px;width:208px;height:167px;background:var(--white);border-radius:10px;box-shadow:0 6px 22px rgba(20,30,70,.12);padding:62px 16px 0 18px}
.ov-card h3{font-size:15px;font-weight:500;line-height:20px;margin-bottom:6px}
.ov-card p{font-size:11.5px;line-height:18px;color:var(--muted)}
.ico{position:absolute;width:62px;height:62px;border-radius:12px;display:flex;align-items:center;justify-content:center}
.ov-card .ico{top:-30px;left:18px}

/* solutions */
.sol-card{position:absolute;background:var(--white);border-radius:8px;box-shadow:0 6px 22px rgba(20,30,70,.12);padding:70px 16px 0 15px}
.sol-card h3{font-size:14px;font-weight:600;margin-bottom:6px}
.sol-card p{font-size:11.5px;line-height:18.5px;color:var(--muted)}
.sol-card .mark{position:absolute;top:14px;left:15px}
.sol-card .go{position:absolute;right:10px;bottom:10px;width:24px;height:24px;border-radius:4px;background:var(--teal);display:flex;align-items:center;justify-content:center}

/* characteristics */
.feat-ico{position:absolute;width:72px;height:72px;border-radius:50%;display:flex;align-items:center;justify-content:center}
.feat-label{position:absolute;font-size:14px;line-height:21px;color:var(--text)}

/* insights */
.post{position:absolute;background:var(--white);border-radius:8px;box-shadow:0 6px 22px rgba(20,30,70,.1)}
.post .thumb{position:absolute;border-radius:8px}
.meta{display:flex;align-items:center;gap:6px;font-size:9.5px;color:var(--text);white-space:nowrap}
.meta .cal{width:13px;height:12px;border-radius:2px;background:var(--blue)}
.meta .who{width:11px;height:12px;position:relative}
.post h4{font-weight:500;color:var(--text)}
.more{display:inline-block;border:1px solid var(--orange);color:var(--orange);border-radius:5px;font-size:10px;text-transform:uppercase;padding:5px 14px;font-weight:500}

/* cta */
.cta{position:absolute;top:3574px;left:142px;width:916px;height:373px;border-radius:28px;background:linear-gradient(110deg,#10a28c 0%,#0b7fa6 55%,#0b59a8 100%);overflow:hidden}
.cta-photo{position:absolute;top:0;right:0;width:410px;height:373px;border-radius:50% 28px 28px 60% / 40% 28px 28px 30%;background:linear-gradient(135deg,#d9dde6 0%,#9aa6bb 40%,#3d4a66 75%,#1d2740 100%)}
.cta h2{position:absolute;top:124px;left:47px;color:var(--white);font-size:36px;line-height:42px;font-weight:400}
.cta h2 b{font-weight:600}
.cta p{position:absolute;top:216px;left:47px;color:var(--white);font-size:11.5px;line-height:20px;width:460px}
.cta .tag{position:absolute;top:72px;left:47px;border:1px solid rgba(255,255,255,.7);color:var(--white);border-radius:20px;font-size:11px;padding:5px 20px;text-transform:uppercase}

/* footer */
.footer{position:absolute;top:4120px;left:0;width:1200px;height:395px;background:var(--navy-deep)}
.f-col{position:absolute;color:var(--white)}
.f-col h5{font-size:17px;font-weight:500;margin-bottom:14px}
.f-col li{list-style:none;font-size:13px;line-height:28px}
.f-row{display:flex;gap:12px;font-size:12.5px;line-height:20px;margin-bottom:14px}
.soc{display:flex;align-items:center;gap:10px;font-size:12.5px;margin-bottom:16px}
.soc i{width:28px;height:28px;border-radius:50%;display:block}
</style>
</head>
<body>
<div class="page">

  <!-- Header -->
  <header class="header">
    <div class="brand abs" style="top:24px;left:93px;font-size:24px;color:var(--navy)"><span class="dot"></span>QP FIDUCIARY</div>
    <nav class="nav"><span>PLATFORM</span><span>SOLUTIONS</span><span>INSIGHTS</span><span>COMPANY</span><span>CONTACT</span></nav>
    <a class="btn" style="top:18px;left:788px;width:270px;height:45px;justify-content:center;padding:0">Request A Technical Walkthrough</a>
  </header>

  <!-- Hero -->
  <div class="hero-photo" role="img" aria-label="Photo of a team in a meeting room reviewing financial charts on a screen"></div>
  <div class="hero-shade"></div>
  <h1 class="hero-title">Actuarial <b>Software</b> For<br>Structured, Auditable<br><b>Financial Analysis.</b></h1>
  <p class="hero-sub">QP Fiduciary Develops Software That Translates Established Actuarial Methodologies Into Disciplined, Decision-Ready Tools</p>
  <a class="btn" style="top:434px;left:91px;width:303px;height:42px">Request A Technical Walkthrough<span class="arrow"><svg width="16" height="12" viewBox="0 0 16 12"><path d="M1 6h13M9 1l5 5-5 5" stroke="#0b1b4a" stroke-width="2" fill="none"/></svg></span></a>
  <svg class="abs" style="top:520px;left:0" width="1200" height="190" viewBox="0 0 1200 190">
    <path d="M0 100 C250 175 650 150 1200 30 L1200 190 L0 190 Z" fill="#fff"/>
    <path d="M0 90 C240 170 650 140 1200 20 L1200 40 C660 150 260 185 0 125 Z" fill="var(--orange)"/>
  </svg>

  <!-- Platform overview -->
  <span class="badge" style="top:776px">Platform Overview</span>
  <h2 class="section-title" style="top:810px">Built For Actuarial <b>Excellence</b></h2>
  <p class="section-desc" style="top:866px">Our Platform Delivers Structured Workflows, Transparent Assumptions, And Complete Auditability<br>—Enabling Confident, Governance-Ready Financial Analysis.</p>

  <div class="ov-card" style="left:142px">
    <div class="ico" style="background:linear-gradient(135deg,#1a8ae0,#0054AA)"><svg width="36" height="32" viewBox="0 0 36 32" fill="none" stroke="#fff" stroke-width="2"><rect x="2" y="2" width="32" height="20" rx="2"/><path d="M2 8h32M8 27h20M18 22v5"/><rect x="8" y="12" width="6" height="5"/><rect x="22" y="12" width="6" height="5"/></svg></div>
    <h3>Structured Workflows</h3>
    <p>Disciplined Processes That Guide Analysis From Input To Output With Clear, Repeatable Steps.</p>
  </div>
  <div class="ov-card" style="left:377px">
    <div class="ico" style="background:linear-gradient(135deg,#F2A743,#EE7325)"><svg width="34" height="34" viewBox="0 0 34 34" fill="none" stroke="#fff" stroke-width="2"><circle cx="17" cy="17" r="13"/><path d="M10 20l6-8 8 6"/></svg></div>
    <h3>Transparency<br>of Assumptions</h3>
    <p>Every Assumption Is Documented, Visible, And Traceable Throughout…</p>
  </div>
  <div class="ov-card" style="left:613px">
    <div class="ico" style="background:linear-gradient(135deg,#1b3a7a,#0b1b4a)"><svg width="32" height="34" viewBox="0 0 32 34" fill="none" stroke="#fff" stroke-width="2"><rect x="3" y="2" width="20" height="26" rx="2"/><path d="M8 9h10M8 14h10"/><circle cx="22" cy="24" r="7"/><path d="M19 24l2 2 4-4"/></svg></div>
    <h3>Auditability</h3>
    <p>Complete Audit Trails With Version Control And Comprehensive Documentation At Every Step.</p>
  </div>
  <div class="ov-card" style="left:850px">
    <div class="ico" style="background:linear-gradient(135deg,#2bbf9c,#109e8c)"><svg width="34" height="32" viewBox="0 0 34 32" fill="none" stroke="#fff" stroke-width="2"><path d="M3 14L17 3l14 11M7 12v16h20V12"/><circle cx="17" cy="19" r="4"/></svg></div>
    <h3>Governance</h3>
    <p>Built-In Controls And Approval Workflows That Ensure Regulatory Compliance.</p>
  </div>

  <!-- Solutions -->
  <svg class="abs" style="top:1209px;left:0" width="1200" height="610" viewBox="0 0 1200 610">
    <path d="M0 95 Q600 -10 1200 95 L1200 575 Q600 630 0 550 Z" fill="var(--band)"/>
    <ellipse cx="790" cy="270" rx="190" ry="120" fill="none" stroke="var(--teal)" stroke-width="16"/>
  </svg>
  <span class="badge" style="top:1410px;left:215px">Our Solutions</span>
  <h2 class="abs" style="top:1448px;left:142px;font-size:39px;line-height:43px;font-weight:400">Comprehensive<br><b style="font-weight:600">Actuarial Suite</b></h2>
  <p class="abs" style="top:1543px;left:142px;font-size:12.5px;line-height:21px;width:370px">Three Integrated Solution Areas Designed To Address The Full Spectrum Of Actuarial Analysis Needs.</p>
  <a class="btn" style="top:1608px;left:142px;width:305px;height:44px">Request A Technical Walkthrough<span class="arrow"><svg width="16" height="12" viewBox="0 0 16 12"><path d="M1 6h13M9 1l5 5-5 5" stroke="#0b1b4a" stroke-width="2" fill="none"/></svg></span></a>

  <div class="sol-card" style="top:1328px;left:547px;width:245px;height:222px">
    <svg class="mark" width="46" height="46" viewBox="0 0 46 46" fill="none" stroke="#0054AA" stroke-width="2.2"><rect x="8" y="3" width="22" height="28" rx="2"/><path d="M13 10h12M13 16h12M13 22h8"/><circle cx="33" cy="33" r="9"/><path d="M33 28v10M30 31h5M30 35h5"/><path d="M3 43h20"/></svg>
    <h3>Reserving &amp; Valuation</h3>
    <p>Comprehensive Reserve Calculations And Liability Valuations With Transparent Methodology Documentation And Multi-Standard Support.</p>
    <span class="go"><svg width="10" height="10" viewBox="0 0 10 10"><path d="M2 8l6-6M3 2h5v5" stroke="#fff" stroke-width="1.6" fill="none"/></svg></span>
  </div>
  <div class="sol-card" style="top:1328px;left:811px;width:247px;height:222px">
    <svg class="mark" width="46" height="46" viewBox="0 0 46 46" fill="none" stroke="#0054AA" stroke-width="2.2"><path d="M5 20L20 5h14v14L19 34z"/><circle cx="28" cy="11" r="3"/><path d="M14 20l6 6"/><circle cx="33" cy="34" r="9"/><path d="M30 34h6"/></svg>
    <h3>Pricing</h3>
    <p>Sophisticated Pricing Models That Balance Profitability Targets With Competitive Positioning And Regulatory Requirements.</p>
    <span class="go"><svg width="10" height="10" viewBox="0 0 10 10"><path d="M2 8l6-6M3 2h5v5" stroke="#fff" stroke-width="1.6" fill="none"/></svg></span>
  </div>
  <div class="sol-card" style="top:1568px;left:687px;width:245px;height:202px">
    <svg class="mark" width="52" height="52" viewBox="0 0 52 52" fill="none" stroke="#0054AA" stroke-width="2.2"><circle cx="30" cy="20" r="12"/><circle cx="30" cy="20" r="5"/><path d="M30 4v4M30 32v4M14 20h4M42 20h4"/><path d="M4 46c4-8 10-12 18-12"/><circle cx="12" cy="32" r="5"/></svg>
    <h3>Enterprise Risk Management</h3>
    <p>Holistic Risk Assessment And Capital Modeling That Integrates Across Business Units And Regulatory Frameworks.</p>
    <span class="go"><svg width="10" height="10" viewBox="0 0 10 10"><path d="M2 8l6-6M3 2h5v5" stroke="#fff" stroke-width="1.6" fill="none"/></svg></span>
  </div>

  <!-- Characteristics -->
  <span class="badge" style="top:1934px">Why Choose Us</span>
  <h2 class="section-title" style="top:1968px">Platform <b>Characteristics</b></h2>
  <p class="section-desc" style="top:2022px">Key Attributes That Set Our Platform Apart In Delivering Reliable, Governance-Ready<br>Actuarial Analysis.</p>

  <svg class="abs" style="top:2090px;left:0" width="1200" height="300" viewBox="0 0 1200 300">
    <g stroke="#c9cfdc" stroke-width="1.5" fill="none">
      <path d="M450 55L501 77"/><path d="M750 55L701 77"/>
      <path d="M450 245L501 214"/><path d="M750 245L701 214"/>
    </g>
    <g fill="#fff" stroke-width="2">
      <circle cx="501" cy="77" r="5" stroke="var(--blue)"/>
      <circle cx="701" cy="77" r="5" stroke="var(--teal)"/>
      <circle cx="501" cy="214" r="5" stroke="var(--teal)"/>
      <circle cx="701" cy="214" r="5" stroke="var(--blue)"/>
    </g>
  </svg>
  <div class="abs" style="top:2169px;left:454px;width:294px;height:140px;border-radius:70px;background:#fff;box-shadow:0 8px 30px rgba(20,30,70,.14);display:flex;align-items:center;justify-content:center">
    <div class="brand" style="font-size:22px;color:var(--navy)"><span class="dot"></span>QP FIDUCIARY</div>
  </div>

  <div class="feat-ico" style="top:2096px;left:381px;background:var(--blue)"><svg width="34" height="34" viewBox="0 0 34 34" fill="none" stroke="#fff" stroke-width="2.2"><circle cx="17" cy="8" r="5"/><path d="M17 13v8M7 29v-8h20v8"/><circle cx="7" cy="30" r="2"/><circle cx="27" cy="30" r="2"/><circle cx="17" cy="30" r="2"/><path d="M17 21v7"/></svg></div>
  <p class="feat-label" style="top:2110px;left:260px;text-align:right;width:106px">Structured<br>Workflows</p>

  <div class="feat-ico" style="top:2096px;left:747px;background:var(--teal)"><svg width="34" height="34" viewBox="0 0 34 34" fill="none" stroke="#fff" stroke-width="2.2"><path d="M4 30h26M8 30V18M14 30V12M20 30V16M26 30V8"/><circle cx="22" cy="22" r="5"/></svg></div>
  <p class="feat-label" style="top:2110px;left:835px">Comparative<br>Analysis Capability</p>

  <div class="feat-ico" style="top:2299px;left:381px;background:var(--teal)"><svg width="34" height="34" viewBox="0 0 34 34" fill="none" stroke="#fff" stroke-width="2.2"><circle cx="17" cy="12" r="8"/><circle cx="17" cy="12" r="3"/><path d="M3 30c4-6 8-8 14-8s10 2 14 8"/></svg></div>
  <p class="feat-label" style="top:2313px;left:210px;text-align:right;width:158px">Multi-Jurisdictional<br>Review Support</p>

  <div class="feat-ico" style="top:2299px;left:747px;background:var(--blue)"><svg width="34" height="34" viewBox="0 0 34 34" fill="none" stroke="#fff" stroke-width="2.2"><path d="M8 28c-2-3-4-6-4-11a13 13 0 0126 0c0 4-2 6-4 8v4"/><ellipse cx="17" cy="16" rx="7" ry="4"/><circle cx="17" cy="16" r="2"/></svg></div>
  <p class="feat-label" style="top:2313px;left:832px">Transparent<br>Assumptions</p>

  <a class="btn" style="top:2418px;left:450px;width:305px;height:44px">Request A Technical Walkthrough<span class="arrow"><svg width="16" height="12" viewBox="0 0 16 12"><path d="M1 6h13M9 1l5 5-5 5" stroke="#0b1b4a" stroke-width="2" fill="none"/></svg></span></a>

  <!-- Insights -->
  <svg class="abs" style="top:2540px;left:0" width="1200" height="900" viewBox="0 0 1200 900">
    <path d="M0 90 Q600 -10 1200 90 L1200 868 Q600 905 0 860 Z" fill="var(--band)"/>
  </svg>
  <span class="badge" style="top:2621px">Insights</span>
  <h2 class="section-title" style="top:2655px;font-weight:300">Insights &amp; Thought <b>Leadership</b></h2>
  <p class="section-desc" style="top:2709px">Key Attributes That Set Our Platform Apart In Delivering Reliable, Governance-Ready<br>Actuarial Analysis.</p>

  <article class="post" style="top:2777px;left:142px;width:448px;height:539px">
    <div class="thumb" role="img" aria-label="Photo of two business professionals meeting beside a glowing lightbulb graphic" style="top:12px;left:12px;width:424px;height:293px;background:linear-gradient(135deg,#0c2a6b,#1a6fd0 50%,#0b1f4f)"></div>
    <div class="meta abs" style="top:326px;left:18px;font-size:11px"><span class="cal"></span>24 JUL 2025 &nbsp;&nbsp;<svg width="12" height="13" viewBox="0 0 12 13"><circle cx="6" cy="4" r="3" fill="#0054AA"/><path d="M0 13c0-4 3-6 6-6s6 2 6 6z" fill="#0054AA"/></svg>AUTHOR: &nbsp;Paul Nkemdi</div>
    <h4 class="abs" style="top:350px;left:18px;font-size:17px;font-weight:600">RBC (Risk-Based Capital)</h4>
    <p class="abs" style="top:385px;left:18px;width:410px;font-size:12px;line-height:22px;color:var(--text)">Harbor Point, 24 July 2025 – <u>QP FIDUCIARY</u> is an independent actuarial consulting firm headquartered in Eastport, Marlow State, with operations in Port Velan, Calder, and a presence in Ostrava Bay under HALDEN ACTUARY LLP. We specialize…</p>
    <span class="more abs" style="top:475px;left:18px;padding:10px 16px;font-size:11px">Read More</span>
  </article>

  <article class="post" style="top:2780px;left:610px;width:448px;height:169px">
    <div class="thumb" role="img" aria-label="Photo of a person writing beside rising financial charts" style="top:10px;left:10px;width:172px;height:149px;background:linear-gradient(135deg,#3a2a24,#b85a3a 55%,#2a3550)"></div>
    <div class="meta abs" style="top:18px;left:200px"><span class="cal"></span>13 JAN 2026 &nbsp;&nbsp;<svg width="11" height="12" viewBox="0 0 12 13"><circle cx="6" cy="4" r="3" fill="#0054AA"/><path d="M0 13c0-4 3-6 6-6s6 2 6 6z" fill="#0054AA"/></svg>AUTHOR: AUREL MBIDA</div>
    <h4 class="abs" style="top:38px;left:200px;width:235px;font-size:13.5px;line-height:20px">Evolution into Technology-Led Actuarial Platform</h4>
    <p class="abs" style="top:82px;left:200px;width:235px;font-size:9.5px;line-height:17px">Harbor Point, January 12, 2026 –<br>QP FIDUCIARY is thrilled to share…</p>
    <span class="more abs" style="top:126px;left:200px">Read More</span>
  </article>

  <article class="post" style="top:2966px;left:610px;width:448px;height:167px">
    <div class="thumb" role="img" aria-label="Illustration with the words financial literacy and inclusion in gold" style="top:10px;left:10px;width:172px;height:147px;background:linear-gradient(135deg,#0e4a4a,#1f6d5a 50%,#c49a3a)"></div>
    <div class="meta abs" style="top:18px;left:200px"><span class="cal"></span>18 JUN 2025 &nbsp;&nbsp;<svg width="11" height="12" viewBox="0 0 12 13"><circle cx="6" cy="4" r="3" fill="#0054AA"/><path d="M0 13c0-4 3-6 6-6s6 2 6 6z" fill="#0054AA"/></svg>AUTHOR: SERGE TANGWA</div>
    <h4 class="abs" style="top:38px;left:200px;width:240px;font-size:13.5px;line-height:21px">Financial Literacy and Inclusion: Leveraging actuarial expertise to improve financial understanding…</h4>
    <span class="more abs" style="top:128px;left:200px">Read More</span>
  </article>

  <article class="post" style="top:3152px;left:610px;width:448px;height:166px">
    <div class="thumb" role="img" aria-label="Photo of an audience at an insurance innovation forum with a large stage screen" style="top:10px;left:10px;width:172px;height:146px;background:linear-gradient(135deg,#0f2f50,#1c7fa5 50%,#16223c)"></div>
    <div class="meta abs" style="top:18px;left:200px"><span class="cal"></span>27 MAR 2025 &nbsp;&nbsp;<svg width="11" height="12" viewBox="0 0 12 13"><circle cx="6" cy="4" r="3" fill="#0054AA"/><path d="M0 13c0-4 3-6 6-6s6 2 6 6z" fill="#0054AA"/></svg>AUTHOR: Nadia</div>
    <h4 class="abs" style="top:38px;left:200px;width:240px;font-size:13.5px;line-height:21px">Innovation and Regulation in Insurance Insights from the Westland Insurance Industry Innovation Forum</h4>
    <span class="more abs" style="top:126px;left:200px">Read More</span>
  </article>

  <a class="btn" style="top:3364px;left:510px;width:180px;height:42px">View All Articles<span class="arrow"><svg width="16" height="12" viewBox="0 0 16 12"><path d="M1 6h13M9 1l5 5-5 5" stroke="#0b1b4a" stroke-width="2" fill="none"/></svg></span></a>

  <!-- CTA -->
  <section class="cta">
    <div class="cta-photo" role="img" aria-label="Photo of a hand pointing at bar charts on a laptop screen"></div>
    <span class="tag">Schedule A Demo</span>
    <h2>Ready To Transform<br>Your <b>Actuarial Practice?</b></h2>
    <p>Discover How QP Fiduciary's Platform Can Bring Structure, Transparency, And Confidence To Your Financial Analysis Workflows.</p>
    <a class="btn" style="top:282px;left:47px;width:305px;height:44px;background:#fff;color:var(--navy)">Request A Technical Walkthrough<span class="arrow" style="background:linear-gradient(90deg,var(--teal),var(--blue))"><svg width="16" height="12" viewBox="0 0 16 12"><path d="M1 6h13M9 1l5 5-5 5" stroke="#fff" stroke-width="2" fill="none"/></svg></span></a>
  </section>

  <!-- Footer -->
  <svg class="abs" style="top:4045px;left:0" width="1200" height="120" viewBox="0 0 1200 120">
    <path d="M0 95 C380 30 800 5 1200 0 L1200 120 L0 120 Z" fill="var(--orange)"/>
    <path d="M0 125 C380 60 800 40 1200 40 L1200 120 L0 120 Z" fill="var(--navy-deep)"/>
  </svg>
  <footer class="footer">
    <div class="brand abs" style="top:115px;left:142px;font-size:24px;color:var(--white)"><span class="dot"></span>QP FIDUCIARY</div>
    <p class="abs" style="top:163px;left:142px;width:225px;color:var(--white);font-size:11.5px;line-height:19px">Common Approach To Service Delivery Can Be Described Within A Cycle That Involves Defining The Problem, Designing A Solution And Monitoring The Results.</p>

    <div class="f-col" style="top:104px;left:468px">
      <h5>Quick Links</h5>
      <ul><li>Company</li><li>Platform</li><li>Solutions</li><li>Insights</li><li>Contact</li></ul>
    </div>

    <div class="f-col" style="top:104px;left:664px">
      <h5>Contact Details</h5>
      <div class="f-row"><svg width="12" height="16" viewBox="0 0 12 16"><path d="M6 0a6 6 0 016 6c0 4-6 10-6 10S0 10 0 6a6 6 0 016-6z" fill="#fff"/><circle cx="6" cy="6" r="2" fill="#08143a"/></svg><span>410 Harbor Crest Ave,<br>Suite 200,<br>Harbor Point, MP 20417</span></div>
      <div class="f-row"><svg width="13" height="13" viewBox="0 0 24 24"><path d="M6.6 10.8a15 15 0 006.6 6.6l2.2-2.2a1 1 0 011-.3 11 11 0 003.6.6 1 1 0 011 1V20a1 1 0 01-1 1A17 17 0 013 4a1 1 0 011-1h3.5a1 1 0 011 1c0 1.2.2 2.4.6 3.6a1 1 0 01-.3 1z" fill="#fff"/></svg><span>Phone<br>+1(555)010-2486</span></div>
      <div class="f-row"><svg width="14" height="11" viewBox="0 0 14 11"><rect width="14" height="11" rx="1" fill="#fff"/><path d="M1 1l6 5 6-5" stroke="#08143a" stroke-width="1.3" fill="none"/></svg><span>Email<br>contact@qp-fiduciary.example</span></div>
    </div>

    <div class="f-col" style="top:104px;left:943px">
      <h5>Social Media</h5>
      <div class="soc"><i style="background:var(--teal)"></i>Community</div>
      <div class="soc"><i style="border:1.5px solid #fff"></i>Video Channel</div>
      <div class="soc"><i style="border:1.5px solid #fff"></i>Pro Network</div>
      <div class="soc"><i style="border:1.5px solid #fff"></i>Photo Feed</div>
    </div>

    <p class="abs" style="top:358px;left:142px;color:var(--white);font-size:11.5px">© 2026 QP Fiduciary All Rights Reserved.</p>
    <p class="abs" style="top:358px;left:844px;color:var(--white);font-size:11.5px">Price Policy Terms And Conditions</p>
  </footer>

</div>
</body>
</html>
```